I would like a minimalist clean and uncluttered website design.
Initially, I would like to see a front page only and would then like to build on the project front there.
DVQ logo file with no background is attached, can be grey scale if the designer wishes.
I would like the front page to speak about the company's ethos and goals and I will need to put a great deal of thought into this to ensure it has the desired impact with the content on the subsequent pages.
The paragraph below gives a bit of an idea as to what this will include.
"DVQ is a technology company providing approachable IT products and services to business:
With the overwhelming advancements in technology, businesses often find it difficult to determine what is available and what best suits their businesses specific needs.
We can assist business with their IT infrustucture, devices, software in procurement, installation, training, cost control as well as ongoing administration and support. We also keep our Clients informed of new technology and products which can benefit them"
Target Market(s)
Business, Health, Education, Professional Practices. Target age would be around 30 plus either male or female. Office administration level through Managing Directors. English speaking.

```html
<!DOCTYPE html>
<html lang="en">
<head>
<meta charset="utf-8">
<title>Davenquay — IT products and services</title>
<link rel="stylesheet" href="https://fonts.googleapis.com/css2?family=Questrial&family=Open+Sans:ital,wght@0,400;1,300&display=swap">
<style>
:root{
  --green:#8dbb48;
  --navy:#34497f;
  --text:#666;
  --nav:#555;
  --line:#dcdcdc;
  --hero-bg:#f2f2f1;
  --footer-bg:#f4f4f3;
}
*{margin:0;padding:0;box-sizing:border-box}
html,body{width:1200px;height:969px;overflow:hidden;background:#fff}
body{position:relative;font-family:"Open Sans",sans-serif;color:var(--text)}
.site-header{position:absolute;left:0;top:0;width:1200px;height:70px;border-bottom:1px solid var(--line);background:#fff}
.brand{position:absolute;left:185px;top:14px;display:flex;align-items:center;gap:8px}
.brand-mark{width:30px;height:30px;background:var(--green)}
.brand-name{font-family:"Questrial",sans-serif;font-size:22px;color:var(--navy);letter-spacing:2px}
.main-nav a{position:absolute;top:25px;font-family:"Questrial",sans-serif;font-size:14px;color:var(--nav);text-decoration:none}
.main-nav a.active{color:var(--green)}
.nav-underline{position:absolute;left:479px;top:66px;width:81px;height:3px;background:var(--green)}
.account{position:absolute;top:29px;font-size:10px;color:#999;text-decoration:none}
.account-sep{position:absolute;left:964px;top:28px;width:1px;height:14px;background:var(--line)}
.hero{position:absolute;left:0;top:70px;width:1200px;height:388px;background:var(--hero-bg);border-bottom:1px solid var(--line);overflow:hidden}
.hero-photo{position:absolute;left:480px;top:0;width:620px;height:388px;
  background:radial-gradient(ellipse at 62% 55%,#b9a597 0%,#d9cfc7 30%,rgba(242,242,241,0) 70%),
  radial-gradient(ellipse at 78% 70%,#3a3e4a 0%,rgba(242,242,241,0) 45%)}
.hero h1{position:absolute;left:180px;top:116px;font-family:"Questrial",sans-serif;font-weight:400;font-size:28px;color:var(--navy)}
.hero p{position:absolute;left:180px;top:157px;width:400px;font-style:italic;font-weight:300;font-size:16px;line-height:22px;color:#666}
.btn{position:absolute;left:180px;top:224px;width:113px;height:31px;background:var(--green);color:#fff;font-family:"Questrial",sans-serif;font-size:13px;line-height:31px;text-align:center;text-decoration:none}
.slider-dots{position:absolute;left:180px;top:316px;display:flex;gap:3px}
.slider-dots span{width:13px;height:13px;border:1px solid #bbb;border-radius:50%;background:#fff;position:relative}
.slider-dots span.on::after{content:"";position:absolute;left:3px;top:3px;width:5px;height:5px;border-radius:50%;background:var(--navy)}
.ribbon{position:absolute;left:440px;top:500px;width:284px;height:48px}
.ribbon-title{position:absolute;left:470px;top:500px;width:224px;height:38px;line-height:40px;text-align:center;font-family:"Questrial",sans-serif;font-size:25px;color:#fff}
.service{position:absolute;width:240px}
.service h2{display:flex;align-items:center;gap:8px;font-family:"Questrial",sans-serif;font-weight:400;font-size:17px;color:var(--navy);height:24px}
.service h2 svg{flex:none}
.service p{margin-top:14px;font-size:11px;line-height:14.3px;color:var(--text)}
.site-footer{position:absolute;left:0;top:875px;width:1200px;height:94px;background:var(--footer-bg);border-top:1px solid #ececec}
.footer-links{position:absolute;left:178px;top:38px;font-size:10.5px;color:#666}
.footer-links a{color:#555;text-decoration:none}
.footer-links .sep{margin:0 6px}
.social{position:absolute;left:940px;top:38px;display:flex;gap:6px}
.social span{width:15px;height:15px;border-radius:50%;background:#555}
</style>
</head>
<body>
<header class="site-header">
  <div class="brand"><span class="brand-mark"></span><span class="brand-name">DVQ</span></div>
  <nav class="main-nav">
    <a class="active" style="left:500px" href="#">Home</a>
    <a style="left:574px" href="#">Services</a>
    <a style="left:663px" href="#">Project</a>
    <a style="left:743px" href="#">Articles</a>
    <a style="left:826px" href="#">Contact</a>
  </nav>
  <span class="nav-underline"></span>
  <a class="account" style="left:914px" href="#">Log in</a>
  <span class="account-sep"></span>
  <a class="account" style="left:975px" href="#">Sign up</a>
</header>

<section class="hero">
  <div class="hero-photo" role="img" aria-label="Photo of a smiling businesswoman holding a tablet"></div>
  <h1>Welcome to Davenquay</h1>
  <p>DVQ is a technology company providing approachable IT products and services to business.</p>
  <a class="btn" href="#">LEARN MORE</a>
  <div class="slider-dots"><span></span><span class="on"></span><span></span><span></span></div>
</section>

<svg class="ribbon" viewBox="0 0 284 48" aria-hidden="true">
  <polygon points="0,9 40,9 40,48 0,48 10,28" fill="#2c3f70"/>
  <polygon points="284,9 244,9 244,48 284,48 274,28" fill="#2c3f70"/>
  <rect x="30" y="0" width="224" height="38" fill="#34497f"/>
</svg>
<div class="ribbon-title">OUR SERVICES</div>

<div class="service" style="left:180px;top:607px">
  <h2><svg width="24" height="20" viewBox="0 0 24 20"><rect x="1" y="1" width="22" height="14" fill="none" stroke="#34497f" stroke-width="2"/><rect x="10" y="15" width="4" height="3" fill="#34497f"/><rect x="7" y="18" width="10" height="2" fill="#34497f"/></svg>IT infrustucture</h2>
  <p>Lorem Ipsum is simply dummy text of the printing and typesetting industry. Lorem Ipsum dummy text ever since the 1500s...</p>
</div>
<div class="service" style="left:485px;top:607px">
  <h2><svg width="16" height="20" viewBox="0 0 16 20"><rect x="1" y="1" width="14" height="18" rx="2" fill="none" stroke="#34497f" stroke-width="2"/><circle cx="8" cy="16" r="1" fill="#34497f"/></svg>Devices</h2>
  <p>Lorem Ipsum is simply dummy text of the printing and typesetting industry. Lorem Ipsum dummy text ever since the 1500s...</p>
</div>
<div class="service" style="left:789px;top:607px">
  <h2><svg width="22" height="22" viewBox="0 0 22 22"><polygon points="11,1 21,6 11,11 1,6" fill="#5a6fa3"/><polygon points="1,6 11,11 11,21 1,16" fill="#34497f"/><polygon points="21,6 11,11 11,21 21,16" fill="#2c3f70"/></svg>Software</h2>
  <p>Lorem Ipsum is simply dummy text of the printing and typesetting industry. Lorem Ipsum dummy text ever since the 1500s...</p>
</div>
<div class="service" style="left:180px;top:733px">
  <h2><svg width="18" height="22" viewBox="0 0 18 22"><path d="M2 1h14M2 21h14M4 1c0 6 10 7 10 10s-10 4-10 10M14 1c0 6-10 7-10 10s10 4 10 10" fill="none" stroke="#34497f" stroke-width="2"/></svg>Installation</h2>
  <p>Lorem Ipsum is simply dummy text of the printing and typesetting industry. Lorem Ipsum dummy text ever since the 1500s...</p>
</div>
<div class="service" style="left:485px;top:733px">
  <h2><svg width="20" height="22" viewBox="0 0 20 22"><path d="M5 21V12L1 8l2-2 3 3V2h2v7V1h2v8V2h2v7V4h2v10l-3 7z" fill="#34497f"/></svg>Training</h2>
  <p>Lorem Ipsum is simply dummy text of the printing and typesetting industry. Lorem Ipsum dummy text ever since the 1500s...</p>
</div>
<div class="service" style="left:789px;top:733px">
  <h2><svg width="32" height="20" viewBox="0 0 32 20"><rect x="6" y="1" width="25" height="14" fill="none" stroke="#34497f" stroke-width="1.5"/><rect x="1" y="5" width="25" height="14" fill="#fff" stroke="#34497f" stroke-width="2"/><circle cx="13.5" cy="12" r="4" fill="none" stroke="#34497f" stroke-width="1.5"/></svg>Cost control</h2>
  <p>Lorem Ipsum is simply dummy text of the printing and typesetting industry. Lorem Ipsum dummy text ever since the 1500s...</p>
</div>

<footer class="site-footer">
  <div class="footer-links">
    <a href="#">Home</a><span class="sep">|</span><a href="#">Services</a><span class="sep">|</span><a href="#">Project</a><span class="sep">|</span><a href="#">Articles</a><span class="sep">|</span><a href="#">Contact</a><span class="sep">|</span>Copyright © 2013 Davenquay.
  </div>
  <div class="social" aria-label="Social links"><span></span><span></span><span></span><span></span></div>
</footer>
</body>
</html>
```